Professional looking Roller Blind Discount Card that portrays quality at a value for money price!

We need a double sided business card designed as a discount card. Size 90mm wide x 55mm high.We would like it to look professional and portray quality at a value for money price point.I have uploaded a word document with a basic layout with the information we want included on each side of the card. Please put your own thought into the layout.

Contact Information for Business Card

As per word document attached.

```html
<!DOCTYPE html>
<html lang="en">
<head>
<meta charset="utf-8">
<title>Roller Blinds Discount Card</title>
<link href="https://fonts.googleapis.com/css2?family=Poppins:wght@400;500;700;800&family=Oswald:wght@400;700&family=Dancing+Script:wght@600&display=swap" rel="stylesheet">
<style>
  :root {
    --blue: #1f9ad9;
    --blue-deep: #1578c2;
    --blue-light: #5cc2f0;
    --ink: #3d3d3d;
    --paper: #ffffff;
    --backdrop: #e9ecef;
  }
  * { margin: 0; padding: 0; box-sizing: border-box; }
  html, body { width: 1200px; height: 874px; overflow: hidden; }
  body {
    background: var(--backdrop);
    font-family: "Poppins", sans-serif;
    display: flex;
    flex-direction: column;
    align-items: center;
    justify-content: center;
    gap: 24px;
  }
  .card {
    position: relative;
    width: 660px;
    height: 403px;
    background: var(--paper);
    box-shadow: 0 4px 14px rgba(0,0,0,0.12);
    overflow: hidden;
  }
  /* Front */
  .front__title {
    position: absolute; right: 22px; top: 14px;
    font-weight: 800; font-size: 66px; line-height: 1;
    color: var(--blue); letter-spacing: 0.5px;
  }
  .front__subtitle {
    position: absolute; right: 22px; top: 82px;
    font-weight: 500; font-size: 27px; color: var(--ink);
  }
  .front__photo {
    position: absolute; left: 22px; top: 124px;
    width: 392px; height: 258px; border-radius: 22px; overflow: hidden;
    background: linear-gradient(135deg, #7a6a5c 0%, #8aa37a 40%, #c9d6c0 70%, #8f7a64 100%);
  }
  .front__call {
    position: absolute; left: 0; right: 0; bottom: 0; height: 54px;
    background: var(--blue);
    color: #fff; font-size: 22px; font-weight: 500;
    display: flex; align-items: center; justify-content: center; gap: 8px;
  }
  .front__call strong { font-weight: 800; font-size: 25px; }
  .bubble { position: absolute; left: 440px; top: 212px; width: 200px; height: 110px; }
  .bubble__text {
    position: absolute; left: 440px; top: 228px; width: 190px;
    font-family: "Dancing Script", cursive; font-size: 22px; line-height: 1.05;
    color: #fff; text-align: center;
  }
  .brand {
    position: absolute; right: 24px; bottom: 22px;
    display: flex; align-items: center; gap: 10px;
    font-weight: 700; font-size: 22px; color: var(--blue-deep);
  }
  .brand__dot { width: 16px; height: 16px; border-radius: 50%; background: var(--blue-deep); }
  /* Back */
  .offer { position: absolute; left: 30px; top: 24px; }
  .offer__headline { font-weight: 800; font-size: 76px; line-height: 1; color: var(--blue); }
  .offer__product { font-weight: 500; font-size: 27px; line-height: 1.1; color: var(--ink); margin-top: 6px; }
  .offer__types { font-size: 18px; line-height: 1.3; color: var(--ink); margin-top: 18px; }
  .offer__types .sep { color: var(--blue); }
  .offer__cta { font-size: 27px; line-height: 1.15; color: var(--ink); margin-top: 16px; font-weight: 500; }
  .offer__phone { color: var(--blue); font-weight: 700; }
  .badge { position: absolute; width: 168px; height: 168px; }
  .badge--free { left: 428px; top: 40px; }
  .badge--best { left: 284px; top: 216px; }
  .badge--family { left: 468px; top: 222px; }
  .badge text { font-family: "Oswald", sans-serif; fill: #fff; text-anchor: middle; }
  .badge .badge__word { font-weight: 700; font-size: 46px; }
  .badge .badge__line { font-weight: 400; font-size: 13px; }
</style>
</head>
<body>

<section class="card card--front">
  <div class="front__title">ROLLER BLINDS</div>
  <div class="front__subtitle">FREE in Home Meacure &amp; Quote</div>
  <div class="front__photo" role="img" aria-label="Photo of a sunroom with open roller blinds looking out to a green garden">
    <div class="front__call">CALL <strong>0400 555 123</strong> TODAY!</div>
  </div>
  <svg class="bubble" viewBox="0 0 200 110" aria-hidden="true">
    <defs>
      <linearGradient id="bubbleFill" x1="0" y1="0" x2="0" y2="1">
        <stop offset="0" stop-color="#5cc2f0"/>
        <stop offset="1" stop-color="#1578c2"/>
      </linearGradient>
    </defs>
    <ellipse cx="95" cy="48" rx="92" ry="44" fill="url(#bubbleFill)"/>
    <path d="M150 80 L178 106 L128 88 Z" fill="#1578c2"/>
  </svg>
  <div class="bubble__text">Huge Selection<br>of Fabrics</div>
  <div class="brand"><span class="brand__dot"></span>B&amp;K INTERIORS</div>
</section>

<section class="card card--back">
  <div class="offer">
    <div class="offer__headline">25% OFF</div>
    <div class="offer__product">QUALITY CUSTOM<br>MADE ROLLER BLINDS</div>
    <div class="offer__types">BLOCKOUT <span class="sep">•</span> SCREEN<br>LIGHTFILTERING</div>
    <div class="offer__cta">CALL<br><span class="offer__phone">0400 555 123</span><br>TODAY!</div>
  </div>

  <svg class="badge badge--free" viewBox="0 0 200 200" aria-label="Free in home measure and quote">
    <defs>
      <radialGradient id="sealFill" cx="0.4" cy="0.3" r="0.8">
        <stop offset="0" stop-color="#8fd6f7"/>
        <stop offset="0.5" stop-color="#2aa3e0"/>
        <stop offset="1" stop-color="#1570b8"/>
      </radialGradient>
    </defs>
    <circle cx="100" cy="100" r="90" fill="none" stroke="#2596d6" stroke-width="10" stroke-dasharray="5 4"/>
    <circle cx="100" cy="100" r="88" fill="url(#sealFill)"/>
    <text class="badge__word" x="100" y="114">FREE</text>
    <text class="badge__line" x="100" y="136">IN HOME MEASURE &amp; QUOTE</text>
  </svg>

  <svg class="badge badge--best" viewBox="0 0 200 200" aria-label="Best price guarantee">
    <circle cx="100" cy="100" r="90" fill="none" stroke="#2596d6" stroke-width="10" stroke-dasharray="5 4"/>
    <circle cx="100" cy="100" r="88" fill="url(#sealFill)"/>
    <text class="badge__word" x="100" y="114">BEST</text>
    <text class="badge__line" x="100" y="136" style="font-size:15px">PRICE GUARANTEE</text>
  </svg>

  <svg class="badge badge--family" viewBox="0 0 200 200" aria-label="Family owned and operated">
    <circle cx="100" cy="100" r="90" fill="none" stroke="#2596d6" stroke-width="10" stroke-dasharray="5 4"/>
    <circle cx="100" cy="100" r="88" fill="url(#sealFill)"/>
    <text class="badge__word" x="100" y="114" style="font-size:40px">FAMILY</text>
    <text class="badge__line" x="100" y="136" style="font-size:15px">OWNED &amp; OPERATED</text>
  </svg>
</section>

</body>
</html>
```